1 Page for Computer Repair Website

Looking for a 1 page website with a design that compliments the business card and pamphlet that have already been made (attached files). It should look business professional and easy to read. Email and phone number should be somewhere near the top of the website, visible when the page loads. I don't want any forms for people to mess with. No "Contact Us" form or entering in email for newsletter. Customers will just be looking at this site to confirm we are professionals and have our business in order.

Target Market(s)

Home and small business

Industry/Entity Type

Computer Repair

Coding

Coded - Design and coding required

Number of Pages Required

1 page

Font styles to use
Other font styles liked:
• Helvetica variations used in pamphlet and card

Colors
0455a3
cfdeed
85abd2
3276b5
85cae6
ffffff

Requirements
Must have
• Compliment the pamphlet and business card in color choices and font use. Pleasing to the eye and easy to read through categories and text.
Should not have
• Forms. No "enter name and email here" or anything of the sort.

```html
<!DOCTYPE html>
<html lang="en">
<head>
<meta charset="utf-8">
<title>Northbyte Computer Services</title>
<link href="https://fonts.googleapis.com/css2?family=Roboto:wght@300;400;500;700&display=swap" rel="stylesheet">
<style>
:root{
  --blue:#0455a3;
  --blue-mid:#3276b5;
  --blue-soft:#85abd2;
  --blue-pale:#cfdeed;
  --sky:#85cae6;
  --white:#ffffff;
  --navy:#0b2e63;
  --navy-dark:#0a1f40;
  --ink:#1f2a37;
  --muted:#5c6673;
  --hero-bg:#f1e9eb;
  --why-bg:#f3f4f6;
  --footer-bg:#1c1c1e;
  --card-grey:#8d9096;
}
*{margin:0;padding:0;box-sizing:border-box}
html,body{width:1200px;height:2752px;overflow:hidden}
body{font-family:"Roboto",Helvetica,Arial,sans-serif;color:var(--ink);background:var(--white)}
section,header,footer{position:relative;width:1200px;overflow:hidden}

/* Header */
.site-header{height:150px;display:flex;align-items:center;justify-content:space-between;padding:0 175px}
.contact-chip{display:flex;align-items:center;gap:18px;font-size:20px;font-weight:500;color:var(--ink)}
.contact-chip .chip-icon{width:34px;height:34px;border-radius:50%;background:var(--blue);display:flex;align-items:center;justify-content:center}
.brand{text-align:center;color:var(--navy-dark);font-weight:400}
.brand .brand-name{font-size:58px;letter-spacing:2px;line-height:1}
.brand .brand-sub{font-size:22px;margin-top:4px}

/* Hero */
.hero{height:650px;background:var(--hero-bg)}
.hero-text{position:absolute;left:50px;top:225px;width:560px}
.hero-title{font-size:42px;font-weight:700;color:var(--blue)}
.hero-sub{font-size:28px;color:var(--navy-dark);margin-top:4px}
.hero-copy{font-size:13px;line-height:20px;color:var(--muted);margin-top:14px}
.btn{display:inline-block;background:var(--navy);color:var(--white);font-size:13px;font-weight:500;padding:14px 26px;letter-spacing:.5px}
.hero .btn{margin-top:24px}
.hero-photo{position:absolute;right:40px;top:70px;width:540px;height:520px;background:linear-gradient(150deg,#e9e6ea,#c9ced6 55%,#6d7684)}

/* About */
.about{height:290px}
.about-photo{position:absolute;left:0;top:20px;width:210px;height:220px;background:radial-gradient(circle at 50% 50%,#7fa35a,#3d5a2c 60%,#b8bcc2)}
.about-text{position:absolute;left:225px;top:20px;width:930px}
.section-title{font-size:34px;font-weight:500;color:var(--navy-dark)}
.about-copy{font-size:13px;line-height:20px;color:var(--muted);margin-top:12px}
.about .btn{margin-top:22px;padding:12px 20px}

/* Services */
.services{height:1160px;background:linear-gradient(180deg,#1a2333,#0f1826 40%,#1b2533)}
.services .section-title{color:var(--white);text-align:center;padding-top:58px;font-size:36px}
.service-grid{position:absolute;left:52px;top:138px;width:1096px;display:grid;grid-template-columns:1fr 1fr;column-gap:28px;row-gap:24px}
.service-card{position:relative;height:176px;background:var(--navy);display:flex;padding:28px 30px 0 26px;gap:28px}
.service-card.is-active{background:var(--card-grey)}
.service-icon{flex:0 0 80px;height:80px;border:2px solid var(--white);border-radius:50%;display:flex;align-items:center;justify-content:center;margin-top:14px}
.is-active .service-icon{background:var(--white);border-color:var(--white)}
.service-name{font-size:22px;font-weight:400;color:var(--white);margin-top:4px}
.service-copy{font-size:12px;line-height:17px;color:var(--blue-pale);margin-top:10px;width:380px}
.is-active .service-copy{color:var(--white)}
.card-arrow{position:absolute;right:0;bottom:0;width:34px;height:28px;background:#c9ccd1;display:flex;align-items:center;justify-content:center}
.is-active .card-arrow{background:var(--navy)}

/* Why */
.why{height:370px;background:var(--why-bg)}
.why .section-title{text-align:center;padding-top:42px;font-size:34px}
.why-list{list-style:none;position:absolute;left:120px;top:120px;width:960px}
.why-list li{display:flex;align-items:center;gap:16px;font-size:13px;color:var(--muted);height:30px}
.why-list .tick{width:18px;height:18px;background:var(--blue);display:flex;align-items:center;justify-content:center;flex:0 0 18px}

/* Footer */
.site-footer{height:142px;background:var(--footer-bg);color:var(--white)}
.footer-contacts{display:flex;justify-content:space-between;align-items:center;padding:18px 40px 0 40px;height:82px}
.footer-item{display:flex;align-items:center;gap:16px;font-size:22px}
.footer-item .ring{width:40px;height:40px;border:2px solid var(--white);border-radius:50%;display:flex;align-items:center;justify-content:center}
.footer-bottom{position:absolute;left:0;bottom:0;width:1200px;height:58px;background:#121214;text-align:center;font-size:11px;color:#b8bcc2;padding-top:14px;line-height:16px}
.social{position:absolute;right:40px;top:16px;display:flex;gap:8px}
.social span{width:26px;height:26px;border-radius:50%;background:#3a3d44;display:block}
</style>
</head>
<body>

<header class="site-header">
  <div class="contact-chip">
    <span>info@company.com</span>
    <span class="chip-icon"><svg width="16" height="12" viewBox="0 0 16 12"><rect x="0.5" y="0.5" width="15" height="11" fill="none" stroke="#fff"/><path d="M1 1l7 6 7-6" fill="none" stroke="#fff"/></svg></span>
  </div>
  <div class="brand">
    <div class="brand-name">NORTHBYTE</div>
    <div class="brand-sub">Computer Services</div>
  </div>
  <div class="contact-chip">
    <span class="chip-icon"><svg width="16" height="16" viewBox="0 0 24 24"><path d="M6.6 10.8a15.1 15.1 0 006.6 6.6l2.2-2.2a1 1 0 011-.25 11.4 11.4 0 003.6.57 1 1 0 011 1V20a1 1 0 01-1 1A17 17 0 013 4a1 1 0 011-1h3.5a1 1 0 011 1c0 1.25.2 2.45.57 3.6a1 1 0 01-.25 1z" fill="#fff"/></svg></span>
    <span>123-456-7890</span>
  </div>
</header>

<section class="hero">
  <div class="hero-text">
    <h1 class="hero-title">Any computer problems?</h1>
    <p class="hero-sub">Receive instant service!</p>
    <p class="hero-copy">Slow startup, frozen screens or a laptop that will not charge? Our certified technicians diagnose the fault quickly, explain the fix in plain words and get your machine working again, often the same day, at your home, your office or our service counter. Every repair is backed by a clear written quote and a ninety day guarantee on parts and labour.</p>
    <span class="btn">READ MORE</span>
  </div>
  <div class="hero-photo" role="img" aria-label="Photo of a technician's arm reaching out of a computer monitor holding a wrench, with keyboard and mouse on a desk"></div>
</section>

<section class="about">
  <div class="about-photo" role="img" aria-label="Illustration of computer components: motherboard, cooling fan and hardware parts"></div>
  <div class="about-text">
    <h2 class="section-title">About Us</h2>
    <p class="about-copy">We are a locally owned repair shop serving homes and small businesses across the region for more than twelve years. Our team works on desktops, laptops, printers and small office networks of every brand. We keep honest prices, explain every step before we start and return your equipment clean, tested and ready to use. Customers come back to us because we treat their data and their time with care.</p>
    <span class="btn">READ MORE</span>
  </div>
</section>

<section class="services">
  <h2 class="section-title">Our Services</h2>
  <div class="service-grid">
    <article class="service-card">
      <div class="service-icon"><svg width="38" height="34" viewBox="0 0 38 34"><rect x="2" y="2" width="34" height="22" fill="none" stroke="#fff" stroke-width="3"/><rect x="14" y="26" width="10" height="4" fill="#fff"/><rect x="9" y="30" width="20" height="3" fill="#fff"/></svg></div>
      <div><h3 class="service-name">PC/Laptop Hardware Repair</h3><p class="service-copy">Broken screens, failed drives, worn keyboards and dead power ports replaced with quality parts and tested before return.</p></div>
      <span class="card-arrow"><svg width="8" height="12" viewBox="0 0 8 12"><path d="M1 1l5 5-5 5" fill="none" stroke="#fff" stroke-width="2"/></svg></span>
    </article>
    <article class="service-card is-active">
      <div class="service-icon"><svg width="38" height="38" viewBox="0 0 38 38"><circle cx="19" cy="19" r="16" fill="var(--navy)"/><circle cx="19" cy="19" r="5" fill="#fff"/><path d="M19 5v8M19 25v8M5 19h8M25 19h8" stroke="#fff" stroke-width="3"/></svg></div>
      <div><h3 class="service-name">Malware Removal</h3><p class="service-copy">Viruses, spyware and pop-ups cleaned out completely, followed by protection settings that keep your computer safe going forward.</p></div>
      <span class="card-arrow"><svg width="8" height="12" viewBox="0 0 8 12"><path d="M1 1l5 5-5 5" fill="none" stroke="#fff" stroke-width="2"/></svg></span>
    </article>
    <article class="service-card">
      <div class="service-icon"><svg width="40" height="36" viewBox="0 0 40 36"><circle cx="14" cy="20" r="9" fill="none" stroke="#fff" stroke-width="5" stroke-dasharray="4 3"/><circle cx="14" cy="20" r="3" fill="#fff"/><circle cx="30" cy="9" r="6" fill="none" stroke="#fff" stroke-width="4" stroke-dasharray="3 2"/></svg></div>
      <div><h3 class="service-name">Hard/Software Upgrades</h3><p class="service-copy">More memory, faster solid state drives and current operating systems installed so older machines feel new again.</p></div>
      <span class="card-arrow"><svg width="8" height="12" viewBox="0 0 8 12"><path d="M1 1l5 5-5 5" fill="none" stroke="#fff" stroke-width="2"/></svg></span>
    </article>
    <article class="service-card">
      <div class="service-icon"><svg width="30" height="38" viewBox="0 0 30 38"><path d="M2 2h18l8 8v26H2z" fill="none" stroke="#fff" stroke-width="3"/><path d="M8 18h14M8 24h14M8 30h10" stroke="#fff" stroke-width="2.5"/></svg></div>
      <div><h3 class="service-name">Date Migration</h3><p class="service-copy">Files, photos, email and settings moved safely from your old computer to the new one without anything left behind.</p></div>
      <span class="card-arrow"><svg width="8" height="12" viewBox="0 0 8 12"><path d="M1 1l5 5-5 5" fill="none" stroke="#fff" stroke-width="2"/></svg></span>
    </article>
    <article class="service-card">
      <div class="service-icon"><svg width="38" height="38" viewBox="0 0 38 38"><circle cx="19" cy="19" r="15" fill="none" stroke="#fff" stroke-width="3"/><circle cx="19" cy="19" r="6" fill="none" stroke="#fff" stroke-width="3"/><path d="M19 4v9M19 25v9M4 19h9M25 19h9" stroke="#fff" stroke-width="3"/></svg></div>
      <div><h3 class="service-name">Clean/tune ups</h3><p class="service-copy">Dust removed, fans checked, startup programs trimmed and updates applied so your system runs cool and quick.</p></div>
      <span class="card-arrow"><svg width="8" height="12" viewBox="0 0 8 12"><path d="M1 1l5 5-5 5" fill="none" stroke="#fff" stroke-width="2"/></svg></span>
    </article>
    <article class="service-card">
      <div class="service-icon"><svg width="38" height="38" viewBox="0 0 38 38"><g fill="#fff"><path d="M19 3l5 9h-10z"/><path d="M19 35l-5-9h10z"/><path d="M3 19l9-5v10z"/><path d="M35 19l-9 5v-10z"/><circle cx="19" cy="19" r="4"/></g></svg></div>
      <div><h3 class="service-name">Date Resue</h3><p class="service-copy">Lost files recovered from failing drives, deleted folders and damaged memory cards whenever the data can be reached.</p></div>
      <span class="card-arrow"><svg width="8" height="12" viewBox="0 0 8 12"><path d="M1 1l5 5-5 5" fill="none" stroke="#fff" stroke-width="2"/></svg></span>
    </article>
    <article class="service-card">
      <div class="service-icon"><svg width="38" height="34" viewBox="0 0 38 34"><path d="M19 2L2 17h5v15h9v-10h6v10h9V17h5z" fill="#fff"/></svg></div>
      <div><h3 class="service-name">In-Home Installation</h3><p class="service-copy">We set up new computers, printers and wireless networks at your home and show you how everything works.</p></div>
      <span class="card-arrow"><svg width="8" height="12" viewBox="0 0 8 12"><path d="M1 1l5 5-5 5" fill="none" stroke="#fff" stroke-width="2"/></svg></span>
    </article>
    <article class="service-card">
      <div class="service-icon"><svg width="26" height="38" viewBox="0 0 26 38"><path d="M16 1L2 22h10l-3 15L24 15H14z" fill="#fff"/></svg></div>
      <div><h3 class="service-name">Remote Support</h3><p class="service-copy">Quick fixes and software help over a secure remote connection, with no need to bring your computer in.</p></div>
      <span class="card-arrow"><svg width="8" height="12" viewBox="0 0 8 12"><path d="M1 1l5 5-5 5" fill="none" stroke="#fff" stroke-width="2"/></svg></span>
    </article>
  </div>
</section>

<section class="why">
  <h2 class="section-title">Why Choose Us</h2>
  <ul class="why-list">
    <li><span class="tick"><svg width="12" height="10" viewBox="0 0 12 10"><path d="M1 5l3.5 3.5L11 1" fill="none" stroke="#fff" stroke-width="2"/></svg></span>Certified technicians with over twelve years of hands-on repair experience.</li>
    <li><span class="tick"><svg width="12" height="10" viewBox="0 0 12 10"><path d="M1 5l3.5 3.5L11 1" fill="none" stroke="#fff" stroke-width="2"/></svg></span>Clear written quotes before any work begins, with no hidden fees.</li>
    <li><span class="tick"><svg width="12" height="10" viewBox="0 0 12 10"><path d="M1 5l3.5 3.5L11 1" fill="none" stroke="#fff" stroke-width="2"/></svg></span>Most repairs finished within one to two business days.</li>
    <li><span class="tick"><svg width="12" height="10" viewBox="0 0 12 10"><path d="M1 5l3.5 3.5L11 1" fill="none" stroke="#fff" stroke-width="2"/></svg></span>Ninety day guarantee on every part and every hour of labour.</li>
    <li><span class="tick"><svg width="12" height="10" viewBox="0 0 12 10"><path d="M1 5l3.5 3.5L11 1" fill="none" stroke="#fff" stroke-width="2"/></svg></span>Your files and personal information stay private and protected.</li>
    <li><span class="tick"><svg width="12" height="10" viewBox="0 0 12 10"><path d="M1 5l3.5 3.5L11 1" fill="none" stroke="#fff" stroke-width="2"/></svg></span>On-site service available for homes and small offices.</li>
    <li><span class="tick"><svg width="12" height="10" viewBox="0 0 12 10"><path d="M1 5l3.5 3.5L11 1" fill="none" stroke="#fff" stroke-width="2"/></svg></span>Friendly support that explains problems in plain, simple language.</li>
  </ul>
</section>

<footer class="site-footer">
  <div class="footer-contacts">
    <div class="footer-item">
      <span class="ring"><svg width="14" height="20" viewBox="0 0 14 20"><path d="M7 1a6 6 0 00-6 6c0 5 6 12 6 12s6-7 6-12a6 6 0 00-6-6z" fill="#fff"/><circle cx="7" cy="7" r="2.2" fill="#1c1c1e"/></svg></span>
      <span>Address Line1, Address Line2<br>Country - 123456</span>
    </div>
    <div class="footer-item">
      <span class="ring"><svg width="18" height="18" viewBox="0 0 24 24"><path d="M6.6 10.8a15.1 15.1 0 006.6 6.6l2.2-2.2a1 1 0 011-.25 11.4 11.4 0 003.6.57 1 1 0 011 1V20a1 1 0 01-1 1A17 17 0 013 4a1 1 0 011-1h3.5a1 1 0 011 1c0 1.25.2 2.45.57 3.6a1 1 0 01-.25 1z" fill="#fff"/></svg></span>
      <span>(123) 456-7890</span>
    </div>
    <div class="footer-item">
      <span class="ring"><svg width="18" height="13" viewBox="0 0 16 12"><rect x="0.5" y="0.5" width="15" height="11" fill="none" stroke="#fff"/><path d="M1 1l7 6 7-6" fill="none" stroke="#fff"/></svg></span>
      <span>info@company.com</span>
    </div>
  </div>
  <div class="footer-bottom">
    Home | About Us | Our Services | Why Us | Contact Us<br>
    © 2024 Northbyte Computer Services. All rights reserved.
    <div class="social"><span></span><span></span><span></span><span></span></div>
  </div>
</footer>

</body>
</html>
```